Fun A1 2012 family planner using clever typography and block colour

I have been looking for an A1 2012 family planner and I have not been able to find one. Hence I would like help to develop such a planner. I plan to print it on matt paper, portrait orientated. I have attached some reference pictures of our 2011 planner. I like interesting typography, clear clean colours and simple illustration. I need space to write in daily events and need the weeks and days to be clearly delineated from each other. Each day cell needs the date and day in it (please refer to the file uploaded for a visual reference confirming this). Each weekend needs some kind of colour/ typographic delineation. I want a design for a year-at-a-view calendar. I plan to print the planner in Sydney, Australia with brightloomprints.com.au and probably to sell printed copies online. The terms & conditions of this project are that I will own the design concept 100% and in perpetuity worldwide once payment has been made. (NB. The attached Work File in Word contains a rough layout and all months, days and dates all typed up to make for quicker design.)

Target Market(s)

Reasonably well heeled family of 4. 2 parents. 2 kids. 2 pets.

Industry/Entity Type

Events

Requirements
Must have
• The calendar must be portrait (not landscape orientated), A1 size. It will be printed on matt paper by brightloomprints.com.au. It must have months running left to right (Jan-Dec) and day/date cells running top to bottom (refer 2011 planner photos in file uploaded). The day/ date cells must be around 3(w)x2(h)cm - big enough to write daily events in. Weekends must be colour/ typographically delineated. 2012 year must be noted as must "A Pebblegate Inc Project" and web address in fine print bottom left hand left hand corner.
Nice to have
• A Pebblegate Inc logo in bottom left hand corder (perhaps Nimble Owl like: http://www.artmarketly.com/design_submission.aspx?designid=731462). Header/Footer space for customisation (e.g. "Hartono-Quist 2012 Planner" or "XYZ Co 2012 Planner".
Should not have
• The calendar should not use photographs or resemble standard or cheesy wall calendars. No watermarks please.

```html
<!DOCTYPE html>
<html lang="en">
<head>
<meta charset="utf-8">
<title>XYZ Co 2012 Planner</title>
<link href="https://fonts.googleapis.com/css2?family=Fredoka:wght@600;700&family=Varela+Round&display=swap" rel="stylesheet">
<style>
:root{
  --orange:#f7941d; --yellow:#fff27a;
  --cyan:#1eb3e6; --sky:#a9dcf3;
  --pink:#ef6aa6; --blush:#f7b6d2;
  --red:#ec1c24; --peach:#fdc89a;
  --green:#86c440; --mint:#d3e7b6;
  --purple:#9a55a3; --lilac:#d8bddc;
  --ink:#58585a; --faint:#cfcfcf;
}
*{box-sizing:border-box;margin:0;padding:0}
html,body{width:847px;height:1200px;overflow:hidden;background:#fff}
.planner{position:relative;width:847px;height:1200px;font-family:"Varela Round",sans-serif;color:var(--ink)}
.months{position:absolute;left:30px;top:8px;display:grid;grid-template-columns:repeat(12,65.7px)}
.month{display:flex;flex-direction:column;align-items:center}
.month-name{width:46px;height:90px;border-radius:23px;background:var(--c);display:flex;align-items:center;justify-content:center;margin-bottom:8px;margin-left:-4px}
.month-name span{transform:rotate(90deg);font-family:"Fredoka",sans-serif;font-weight:700;font-size:33px;letter-spacing:1px;color:#fff;line-height:1}
.days{display:flex;flex-direction:column;gap:2.6px}
.days p{width:63px;height:31px;border:1px solid var(--soft);border-radius:5px;background:#fff;padding:3px 0 0 4px;line-height:1}
.days b{display:block;font-weight:400;font-size:13.5px;color:var(--ink)}
.days i{display:block;font-style:normal;font-size:7.5px;margin-top:1px;color:var(--ink)}
.days p.we{background:var(--hl);border-color:var(--hl)}
.days p.we b,.days p.we i{color:var(--c)}
.jan,.jul{--c:var(--orange);--hl:var(--yellow);--soft:#fff3c4}
.feb,.aug{--c:var(--cyan);--hl:var(--sky);--soft:#d9eff9}
.mar,.sep{--c:var(--pink);--hl:var(--blush);--soft:#fbe0ec}
.apr,.oct{--c:var(--red);--hl:var(--peach);--soft:#fee4cf}
.may,.nov{--c:var(--green);--hl:var(--mint);--soft:#e8f2da}
.jun,.dec{--c:var(--purple);--hl:var(--lilac);--soft:#eddfee}
.jan .we b,.jan .we i,.jul .we b,.jul .we i{color:#f08a12}
.footer-title{position:absolute;left:31px;top:1152px;font-family:"Fredoka",sans-serif;font-weight:600;font-size:28px;letter-spacing:1px;color:#fff;-webkit-text-stroke:1.4px var(--faint)}
</style>
</head>
<body>
<main class="planner">
<div class="months">

<section class="month jan"><h2 class="month-name"><span>JAN</span></h2><div class="days">
<p class="we"><b>01</b><i>Sun</i></p><p><b>02</b><i>Mon</i></p><p><b>03</b><i>Tue</i></p><p><b>02</b><i>Thu</i></p><p><b>05</b><i>Thu</i></p><p><b>06</b><i>Fri</i></p><p class="we"><b>07</b><i>Sat</i></p>
<p class="we"><b>08</b><i>Sun</i></p><p><b>09</b><i>Mon</i></p><p><b>10</b><i>Tue</i></p><p><b>02</b><i>Thu</i></p><p><b>12</b><i>Thu</i></p><p><b>13</b><i>Fri</i></p><p class="we"><b>14</b><i>Sat</i></p>
<p class="we"><b>15</b><i>Sun</i></p><p><b>16</b><i>Mon</i></p><p><b>17</b><i>Tue</i></p><p><b>02</b><i>Thu</i></p><p><b>19</b><i>Thu</i></p><p><b>20</b><i>Fri</i></p><p class="we"><b>21</b><i>Sat</i></p>
<p class="we"><b>22</b><i>Sun</i></p><p><b>23</b><i>Mon</i></p><p><b>24</b><i>Tue</i></p><p><b>02</b><i>Thu</i></p><p><b>26</b><i>Thu</i></p><p><b>27</b><i>Fri</i></p><p class="we"><b>28</b><i>Sat</i></p>
<p class="we"><b>29</b><i>Sun</i></p><p><b>30</b><i>Mon</i></p><p><b>31</b><i>Tue</i></p>
</div></section>

<section class="month feb"><h2 class="month-name"><span>FEB</span></h2><div class="days">
<p><b>01</b><i>Wed</i></p><p><b>02</b><i>Thu</i></p><p><b>01</b><i>Wed</i></p><p class="we"><b>02</b><i>Thu</i></p><p class="we"><b>01</b><i>Wed</i></p><p><b>02</b><i>Thu</i></p><p><b>01</b><i>Wed</i></p>
<p><b>01</b><i>Wed</i></p><p><b>02</b><i>Thu</i></p><p><b>01</b><i>Wed</i></p><p class="we"><b>02</b><i>Thu</i></p><p class="we"><b>01</b><i>Wed</i></p><p><b>02</b><i>Thu</i></p><p><b>01</b><i>Wed</i></p>
<p><b>01</b><i>Wed</i></p><p><b>02</b><i>Thu</i></p><p><b>01</b><i>Wed</i></p><p class="we"><b>02</b><i>Thu</i></p><p class="we"><b>01</b><i>Wed</i></p><p><b>02</b><i>Thu</i></p><p><b>01</b><i>Wed</i></p>
<p><b>01</b><i>Wed</i></p><p><b>02</b><i>Thu</i></p><p><b>01</b><i>Wed</i></p><p class="we"><b>02</b><i>Thu</i></p><p class="we"><b>01</b><i>Wed</i></p><p><b>02</b><i>Thu</i></p><p><b>01</b><i>Wed</i></p>
<p><b>01</b><i>Wed</i></p><p><b>02</b><i>Thu</i></p><p><b>01</b><i>Wed</i></p>
</div></section>

<section class="month mar"><h2 class="month-name"><span>MAR</span></h2><div class="days">
<p><b>01</b><i>Thu</i></p><p><b>02</b><i>Fri</i></p><p class="we"><b>01</b><i>Thu</i></p><p class="we"><b>02</b><i>Fri</i></p><p><b>01</b><i>Thu</i></p><p><b>02</b><i>Fri</i></p><p><b>01</b><i>Thu</i></p>
<p><b>01</b><i>Thu</i></p><p><b>02</b><i>Fri</i></p><p class="we"><b>01</b><i>Thu</i></p><p class="we"><b>02</b><i>Fri</i></p><p><b>01</b><i>Thu</i></p><p><b>02</b><i>Fri</i></p><p><b>01</b><i>Thu</i></p>
<p><b>01</b><i>Thu</i></p><p><b>02</b><i>Fri</i></p><p class="we"><b>01</b><i>Thu</i></p><p class="we"><b>02</b><i>Fri</i></p><p><b>01</b><i>Thu</i></p><p><b>02</b><i>Fri</i></p><p><b>01</b><i>Thu</i></p>
<p><b>01</b><i>Thu</i></p><p><b>02</b><i>Fri</i></p><p class="we"><b>01</b><i>Thu</i></p><p class="we"><b>02</b><i>Fri</i></p><p><b>01</b><i>Thu</i></p><p><b>02</b><i>Fri</i></p><p><b>01</b><i>Thu</i></p>
<p><b>01</b><i>Thu</i></p><p><b>02</b><i>Fri</i></p><p class="we"><b>01</b><i>Thu</i></p>
</div></section>

<section class="month apr"><h2 class="month-name"><span>APR</span></h2><div class="days">
<p class="we"><b>01</b><i>Sun</i></p><p><b>02</b><i>Mon</i></p><p><b>01</b><i>Sun</i></p><p><b>02</b><i>Mon</i></p><p><b>01</b><i>Sun</i></p><p><b>02</b><i>Mon</i></p><p class="we"><b>01</b><i>Sun</i></p>
<p class="we"><b>01</b><i>Sun</i></p><p><b>02</b><i>Mon</i></p><p><b>01</b><i>Sun</i></p><p><b>02</b><i>Mon</i></p><p><b>01</b><i>Sun</i></p><p><b>02</b><i>Mon</i></p><p class="we"><b>01</b><i>Sun</i></p>
<p class="we"><b>01</b><i>Sun</i></p><p><b>02</b><i>Mon</i></p><p><b>01</b><i>Sun</i></p><p><b>02</b><i>Mon</i></p><p><b>01</b><i>Sun</i></p><p><b>02</b><i>Mon</i></p><p class="we"><b>01</b><i>Sun</i></p>
<p class="we"><b>01</b><i>Sun</i></p><p><b>02</b><i>Mon</i></p><p><b>01</b><i>Sun</i></p><p><b>02</b><i>Mon</i></p><p><b>01</b><i>Sun</i></p><p><b>02</b><i>Mon</i></p><p class="we"><b>01</b><i>Sun</i></p>
<p class="we"><b>01</b><i>Sun</i></p><p><b>02</b><i>Mon</i></p><p><b>01</b><i>Sun</i></p>
</div></section>

<section class="month may"><h2 class="month-name"><span>MAY</span></h2><div class="days">
<p><b>01</b><i>Tue</i></p><p><b>02</b><i>Wed</i></p><p><b>01</b><i>Tue</i></p><p><b>02</b><i>Wed</i></p><p class="we"><b>01</b><i>Tue</i></p><p class="we"><b>02</b><i>Wed</i></p><p><b>01</b><i>Tue</i></p>
<p><b>01</b><i>Tue</i></p><p><b>02</b><i>Wed</i></p><p><b>01</b><i>Tue</i></p><p><b>02</b><i>Wed</i></p><p class="we"><b>01</b><i>Tue</i></p><p class="we"><b>02</b><i>Wed</i></p><p><b>01</b><i>Tue</i></p>
<p><b>01</b><i>Tue</i></p><p><b>02</b><i>Wed</i></p><p><b>01</b><i>Tue</i></p><p><b>02</b><i>Wed</i></p><p class="we"><b>01</b><i>Tue</i></p><p class="we"><b>02</b><i>Wed</i></p><p><b>01</b><i>Tue</i></p>
<p><b>01</b><i>Tue</i></p><p><b>02</b><i>Wed</i></p><p><b>01</b><i>Tue</i></p><p><b>02</b><i>Wed</i></p><p class="we"><b>01</b><i>Tue</i></p><p class="we"><b>02</b><i>Wed</i></p><p><b>01</b><i>Tue</i></p>
<p><b>01</b><i>Tue</i></p><p><b>02</b><i>Wed</i></p><p><b>01</b><i>Tue</i></p>
</div></section>

<section class="month jun"><h2 class="month-name"><span>JUN</span></h2><div class="days">
<p><b>01</b><i>Fri</i></p><p class="we"><b>02</b><i>Sat</i></p><p class="we"><b>01</b><i>Fri</i></p><p><b>02</b><i>Sat</i></p><p><b>01</b><i>Fri</i></p><p><b>02</b><i>Sat</i></p><p><b>01</b><i>Fri</i></p>
<p><b>01</b><i>Fri</i></p><p class="we"><b>02</b><i>Sat</i></p><p class="we"><b>01</b><i>Fri</i></p><p><b>02</b><i>Sat</i></p><p><b>01</b><i>Fri</i></p><p><b>02</b><i>Sat</i></p><p><b>01</b><i>Fri</i></p>
<p><b>01</b><i>Fri</i></p><p class="we"><b>02</b><i>Sat</i></p><p class="we"><b>01</b><i>Fri</i></p><p><b>02</b><i>Sat</i></p><p><b>01</b><i>Fri</i></p><p><b>02</b><i>Sat</i></p><p><b>01</b><i>Fri</i></p>
<p><b>01</b><i>Fri</i></p><p class="we"><b>02</b><i>Sat</i></p><p class="we"><b>01</b><i>Fri</i></p><p><b>02</b><i>Sat</i></p><p><b>01</b><i>Fri</i></p><p><b>02</b><i>Sat</i></p><p><b>01</b><i>Fri</i></p>
<p><b>01</b><i>Fri</i></p><p class="we"><b>02</b><i>Sat</i></p><p class="we"><b>01</b><i>Fri</i></p>
</div></section>

<section class="month jul"><h2 class="month-name"><span>JUL</span></h2><div class="days">
<p class="we"><b>01</b><i>Sun</i></p><p><b>02</b><i>Mon</i></p><p><b>01</b><i>Sun</i></p><p><b>02</b><i>Mon</i></p><p><b>01</b><i>Sun</i></p><p><b>02</b><i>Mon</i></p><p class="we"><b>01</b><i>Sun</i></p>
<p class="we"><b>01</b><i>Sun</i></p><p><b>02</b><i>Mon</i></p><p><b>01</b><i>Sun</i></p><p><b>02</b><i>Mon</i></p><p><b>01</b><i>Sun</i></p><p><b>02</b><i>Mon</i></p><p class="we"><b>01</b><i>Sun</i></p>
<p class="we"><b>01</b><i>Sun</i></p><p><b>02</b><i>Mon</i></p><p><b>01</b><i>Sun</i></p><p><b>02</b><i>Mon</i></p><p><b>01</b><i>Sun</i></p><p><b>02</b><i>Mon</i></p><p class="we"><b>01</b><i>Sun</i></p>
<p class="we"><b>01</b><i>Sun</i></p><p><b>02</b><i>Mon</i></p><p><b>01</b><i>Sun</i></p><p><b>02</b><i>Mon</i></p><p><b>01</b><i>Sun</i></p><p><b>02</b><i>Mon</i></p><p class="we"><b>01</b><i>Sun</i></p>
<p class="we"><b>01</b><i>Sun</i></p><p><b>02</b><i>Mon</i></p><p><b>01</b><i>Sun</i></p>
</div></section>

<section class="month aug"><h2 class="month-name"><span>AUG</span></h2><div class="days">
<p><b>01</b><i>Wed</i></p><p><b>02</b><i>Thu</i></p><p><b>01</b><i>Wed</i></p><p class="we"><b>02</b><i>Thu</i></p><p class="we"><b>01</b><i>Wed</i></p><p><b>02</b><i>Thu</i></p><p><b>01</b><i>Wed</i></p>
<p><b>01</b><i>Wed</i></p><p><b>02</b><i>Thu</i></p><p><b>01</b><i>Wed</i></p><p class="we"><b>02</b><i>Thu</i></p><p class="we"><b>01</b><i>Wed</i></p><p><b>02</b><i>Thu</i></p><p><b>01</b><i>Wed</i></p>
<p><b>01</b><i>Wed</i></p><p><b>02</b><i>Thu</i></p><p><b>01</b><i>Wed</i></p><p class="we"><b>02</b><i>Thu</i></p><p class="we"><b>01</b><i>Wed</i></p><p><b>02</b><i>Thu</i></p><p><b>01</b><i>Wed</i></p>
<p><b>01</b><i>Wed</i></p><p><b>02</b><i>Thu</i></p><p><b>01</b><i>Wed</i></p><p class="we"><b>02</b><i>Thu</i></p><p class="we"><b>01</b><i>Wed</i></p><p><b>02</b><i>Thu</i></p><p><b>01</b><i>Wed</i></p>
<p><b>01</b><i>Wed</i></p><p><b>02</b><i>Thu</i></p><p><b>01</b><i>Wed</i></p>
</div></section>

<section class="month sep"><h2 class="month-name"><span>SEP</span></h2><div class="days">
<p class="we"><b>01</b><i>Sat</i></p><p class="we"><b>02</b><i>Sun</i></p><p><b>01</b><i>Sat</i></p><p><b>02</b><i>Sun</i></p><p><b>01</b><i>Sat</i></p><p><b>02</b><i>Sun</i></p><p><b>01</b><i>Sat</i></p>
<p class="we"><b>01</b><i>Sat</i></p><p class="we"><b>02</b><i>Sun</i></p><p><b>01</b><i>Sat</i></p><p><b>02</b><i>Sun</i></p><p><b>01</b><i>Sat</i></p><p><b>02</b><i>Sun</i></p><p><b>01</b><i>Sat</i></p>
<p class="we"><b>01</b><i>Sat</i></p><p class="we"><b>02</b><i>Sun</i></p><p><b>01</b><i>Sat</i></p><p><b>02</b><i>Sun</i></p><p><b>01</b><i>Sat</i></p><p><b>02</b><i>Sun</i></p><p><b>01</b><i>Sat</i></p>
<p class="we"><b>01</b><i>Sat</i></p><p class="we"><b>02</b><i>Sun</i></p><p><b>01</b><i>Sat</i></p><p><b>02</b><i>Sun</i></p><p><b>01</b><i>Sat</i></p><p><b>02</b><i>Sun</i></p><p><b>01</b><i>Sat</i></p>
<p class="we"><b>01</b><i>Sat</i></p><p class="we"><b>02</b><i>Sun</i></p><p><b>01</b><i>Sat</i></p>
</div></section>

<section class="month oct"><h2 class="month-name"><span>OCT</span></h2><div class="days">
<p><b>01</b><i>Mon</i></p><p><b>02</b><i>Tue</i></p><p><b>01</b><i>Mon</i></p><p><b>02</b><i>Tue</i></p><p><b>01</b><i>Mon</i></p><p class="we"><b>02</b><i>Tue</i></p><p class="we"><b>01</b><i>Mon</i></p>
<p><b>01</b><i>Mon</i></p><p><b>02</b><i>Tue</i></p><p><b>01</b><i>Mon</i></p><p><b>02</b><i>Tue</i></p><p><b>01</b><i>Mon</i></p><p class="we"><b>02</b><i>Tue</i></p><p class="we"><b>01</b><i>Mon</i></p>
<p><b>01</b><i>Mon</i></p><p><b>02</b><i>Tue</i></p><p><b>01</b><i>Mon</i></p><p><b>02</b><i>Tue</i></p><p><b>01</b><i>Mon</i></p><p class="we"><b>02</b><i>Tue</i></p><p class="we"><b>01</b><i>Mon</i></p>
<p><b>01</b><i>Mon</i></p><p><b>02</b><i>Tue</i></p><p><b>01</b><i>Mon</i></p><p><b>02</b><i>Tue</i></p><p><b>01</b><i>Mon</i></p><p class="we"><b>02</b><i>Tue</i></p><p class="we"><b>01</b><i>Mon</i></p>
<p><b>01</b><i>Mon</i></p><p><b>02</b><i>Tue</i></p><p><b>01</b><i>Mon</i></p>
</div></section>

<section class="month nov"><h2 class="month-name"><span>NOV</span></h2><div class="days">
<p><b>01</b><i>Thu</i></p><p><b>02</b><i>Fri</i></p><p class="we"><b>01</b><i>Thu</i></p><p class="we"><b>02</b><i>Fri</i></p><p><b>01</b><i>Thu</i></p><p><b>02</b><i>Fri</i></p><p><b>01</b><i>Thu</i></p>
<p><b>01</b><i>Thu</i></p><p><b>02</b><i>Fri</i></p><p class="we"><b>01</b><i>Thu</i></p><p class="we"><b>02</b><i>Fri</i></p><p><b>01</b><i>Thu</i></p><p><b>02</b><i>Fri</i></p><p><b>01</b><i>Thu</i></p>
<p><b>01</b><i>Thu</i></p><p><b>02</b><i>Fri</i></p><p class="we"><b>01</b><i>Thu</i></p><p class="we"><b>02</b><i>Fri</i></p><p><b>01</b><i>Thu</i></p><p><b>02</b><i>Fri</i></p><p><b>01</b><i>Thu</i></p>
<p><b>01</b><i>Thu</i></p><p><b>02</b><i>Fri</i></p><p class="we"><b>01</b><i>Thu</i></p><p class="we"><b>02</b><i>Fri</i></p><p><b>01</b><i>Thu</i></p><p><b>02</b><i>Fri</i></p><p><b>01</b><i>Thu</i></p>
<p><b>01</b><i>Thu</i></p><p><b>02</b><i>Fri</i></p><p class="we"><b>01</b><i>Thu</i></p>
</div></section>

<section class="month dec"><h2 class="month-name"><span>DEC</span></h2><div class="days">
<p class="we"><b>01</b><i>Sat</i></p><p class="we"><b>02</b><i>Sun</i></p><p><b>01</b><i>Sat</i></p><p><b>02</b><i>Sun</i></p><p><b>01</b><i>Sat</i></p><p><b>02</b><i>Sun</i></p><p><b>01</b><i>Sat</i></p>
<p class="we"><b>01</b><i>Sat</i></p><p class="we"><b>02</b><i>Sun</i></p><p><b>01</b><i>Sat</i></p><p><b>02</b><i>Sun</i></p><p><b>01</b><i>Sat</i></p><p><b>02</b><i>Sun</i></p><p><b>01</b><i>Sat</i></p>
<p class="we"><b>01</b><i>Sat</i></p><p class="we"><b>02</b><i>Sun</i></p><p><b>01</b><i>Sat</i></p><p><b>02</b><i>Sun</i></p><p><b>01</b><i>Sat</i></p><p><b>02</b><i>Sun</i></p><p><b>01</b><i>Sat</i></p>
<p class="we"><b>01</b><i>Sat</i></p><p class="we"><b>02</b><i>Sun</i></p><p><b>01</b><i>Sat</i></p><p><b>02</b><i>Sun</i></p><p><b>01</b><i>Sat</i></p><p><b>02</b><i>Sun</i></p><p><b>01</b><i>Sat</i></p>
<p class="we"><b>01</b><i>Sat</i></p><p class="we"><b>02</b><i>Sun</i></p><p><b>01</b><i>Sat</i></p>
</div></section>

</div>
<h1 class="footer-title">XYZ CO 2012 PLANNER</h1>
</main>
</body>
</html>
```